Bluefern Business Services needs a new interactive and interesting website

We need an interesting, professional, modern and functional company website for Bluefern Business Services - a young IT Services company based out of Chennai, India.

Bluefern Business Services is a fully owned subsidiary of Marlow Goods, one of the world's leading direct to consumer wine merchant.

We already have a registered company logo which must feature in the website.

We conceive, design, develop, test, implement and support IT solutions across the entire Marlow Goods IT landscape. For ex : We currently run about 25 e-commerce websites for Marlow Goods on ATG and Dot Net.

We would like to see our corporate colors used in the website. (Burgundy wine and wine green - source: www.bluefernbs-site.com)

We are looking at this website to communicate a fun, friendly and professionally managed company - reaching out to career seekers, prospective customers and general public.

For reference - The company name 'Bluefern' is an inspiration from the Marlow Goods lineage.

The second image with the world map is stickered on our main entrance to the office, I am not sure where this can be used -just putting it out there..

Please note that there are only a few more days to submit designs for this contest  !

I would appreciate if you can help posting your designs in time for our review and consideration.

Thanks.

Reason: Thanks for your inputs. We have a number of designers and a lot to digest and work with in the past few days. There has been a rush of new designs in the last few days Hence we will require more time to process these and make our decision. Hence i am requesting the contest to be open for more days. Regards, Tarun

Target Market(s)

Prospective job seekers who want to know more about the company and also wish to apply for a job vacancy
People wanting to know more about the company in general and our progress
People who want to see what we offer and how we can help them too - prospective customers
Companies that are interested in our IT Captive journey and are looking for a business opportunity

Industry/Entity Type

E-Commerce

Requirements
Must have
• Log In/ Register facility acting as a Single Sign on for Intranet (Employees)

Facility to post job vacancies (with an expiry date) and enable people to apply for a role and upload their CV/Resume.

Facility to Review Job applications

Facility for website visitors to contact Bluefern business Services via an online 'Contact Us' form with a split of job seekers and business opportunities

Gallery facility to upload pictures regarding company events
Nice to have
• Less Cluttered and contemporary design
Some Wine/Vineyard inspirations will be good but not too much, the company is an IT services company

```html
<!DOCTYPE html>
<html lang="en">
<head>
<meta charset="utf-8">
<title>Bluefern Business Services</title>
<link href="https://fonts.googleapis.com/css2?family=Ubuntu:wght@300;400;500;700&display=swap" rel="stylesheet">
<style>
:root{
  --burgundy:#8b0042;
  --green:#78862a;
  --green-dark:#5f6b1e;
  --text:#3a3a3a;
  --muted:#8a8a8a;
  --line:#e6e6e6;
  --page:#ededed;
  --footer:#f4f4f4;
}
*{box-sizing:border-box;margin:0;padding:0}
html,body{width:862px;height:1200px;overflow:hidden}
body{position:relative;background:var(--page);font-family:'Ubuntu',sans-serif;color:var(--text)}
.abs{position:absolute}
.header-band{left:0;top:0;width:862px;height:302px;background:var(--burgundy)}
.brand{left:86px;top:18px;color:#fff;font-weight:500;line-height:1}
.brand .name{font-size:36px;letter-spacing:-.5px;display:flex;align-items:center;gap:8px}
.brand .dot{width:26px;height:26px;border-radius:50%;background:#fff;display:inline-block}
.brand .sub{font-size:20px;margin:6px 0 0 34px}
.callout{left:578px;top:26px;color:#fff;display:flex;gap:8px}
.callout .num{font-size:25px;font-weight:400;line-height:1}
.callout .tag{font-size:13px;margin-top:5px}
.nav{left:79px;top:106px;width:705px;height:32px;display:flex;background:linear-gradient(#fafafa,#e4e4e4);border-radius:3px;overflow:hidden;box-shadow:0 2px 0 rgba(0,0,0,.15)}
.nav a{font-size:11.5px;font-weight:500;color:#333;text-decoration:none;display:flex;align-items:center;justify-content:center;border-left:1px solid #d0d0d0}
.nav a.active{background:linear-gradient(#8d9a34,var(--green-dark));color:#fff;border:none}
.panel{left:79px;top:143px;width:704px;height:846px;background:#fff;box-shadow:0 1px 3px rgba(0,0,0,.15)}
.hero{left:86px;top:150px;width:690px;height:270px;background:linear-gradient(135deg,#c9b3a3 0%,#6f5a50 35%,#2b2523 60%,#bdbdbd 100%)}
.hero-bar{left:86px;top:380px;width:690px;height:40px;background:rgba(40,40,40,.8);color:#fff;font-size:17px;padding:11px 8px}
.upload{left:641px;top:387px;width:118px;height:28px;background:linear-gradient(#fff,#e2e2e2);border-radius:3px;font-size:12px;font-weight:500;color:#333;display:flex;align-items:center;justify-content:center}
.rule-title{font-size:15px;font-weight:500;color:#333;display:flex;align-items:center;gap:8px}
.rule-title::after{content:"";flex:1;height:2px;background:var(--line)}
.welcome h2{font-size:14.5px;font-weight:400;color:#333}
.welcome h2 span{color:var(--burgundy)}
p{font-size:10px;line-height:14.5px;color:var(--muted);font-weight:300}
.more{font-size:8.5px;color:var(--green-dark);display:block;margin-top:4px}
.svc h3{font-size:13px;font-weight:400;color:#444;display:flex;align-items:center;gap:6px;margin-bottom:7px}
.icon{width:24px;height:24px;border-radius:50%;background:var(--green);display:flex;align-items:center;justify-content:center}
.register{left:86px;top:662px;width:690px;height:67px;background:#f6f6f6;border:1px solid #e5e5e5;border-radius:3px}
.field{background:#fff;border:1px solid #ddd;box-shadow:inset 0 2px 2px rgba(0,0,0,.08);font-size:8.5px;color:#aaa;padding:7px;height:23px}
.btn{background:linear-gradient(#8f9c36,var(--green-dark));color:#fff;font-weight:500;border-radius:3px;display:flex;align-items:center;justify-content:center}
.item{border-bottom:1px solid #eee;height:66px}
.item h4{font-size:12.5px;font-weight:400;color:#444;margin-bottom:5px}
.date{width:46px;height:45px;background:var(--burgundy);color:#fff;font-weight:500;font-size:15px;line-height:16px;text-align:center;padding-top:7px}
.footer{left:0;top:1010px;width:862px;height:158px;background:var(--footer);border-top:1px solid #e0e0e0}
.foot h5{font-size:11.5px;font-weight:400;color:#333;margin-bottom:14px}
.foot li{list-style:none;font-size:9px;color:#666;line-height:16.5px}
.vsep{width:1px;height:92px;background:#ddd}
.bottom{left:0;top:1168px;width:862px;height:32px;background:#efefef;border-top:1px solid #e2e2e2;font-size:9px;color:#777;padding:10px 86px;display:flex;justify-content:space-between}
</style>
</head>
<body>
<div class="abs header-band"></div>
<div class="abs brand"><div class="name"><span class="dot"></span>bluefern</div><div class="sub">Business Services</div></div>
<div class="abs callout">
  <svg width="36" height="36" viewBox="0 0 36 36"><path d="M11 6c-4 2-6 6-5 12s5 11 10 13l3-5-4-3c-2-2-3-6-2-9l4-2-1-6z" fill="#fff"/><path d="M22 9a10 10 0 0 1 0 18" stroke="#fff" stroke-width="2.5" fill="none"/></svg>
  <div><div class="num">0160 372 5814</div><div class="tag">Call Us Now For Free Quote</div></div>
</div>
<nav class="abs nav">
  <a class="active" style="width:80px">HOME</a><a style="width:105px">ABOUT US</a><a style="width:103px">CLIENTS</a><a style="width:133px">OUR SERVICES</a><a style="width:90px">CAREERS</a><a style="width:93px">GALLERY</a><a style="width:101px">CONTACT</a>
</nav>
<div class="abs panel"></div>
<div class="abs hero" role="img" aria-label="Photo of a smiling business team gathered around a computer"></div>
<div class="abs hero-bar">Bluefern Business Services</div>
<div class="abs upload">UPLOAD PICTURE</div>

<div class="abs" style="left:86px;top:450px;width:287px;height:2px;background:var(--line)"></div>
<div class="abs rule-title" style="left:381px;top:442px;width:395px">OUR SERVICES</div>

<section class="abs welcome" style="left:86px;top:476px;width:270px">
  <h2>Welcome to <span>Bluefern Business Services</span></h2>
  <p style="margin-top:8px">Lorem ipsum dolor sit amet, consectetur adipiscing elit, sed do eiusmod tempor incididunt ut labore et dolore magna aliqua. Ut enim ad minim veniam, quis nostrud exer-citation ullamco laboris nisi ut aliquip ex ea commodo con-sequat.</p>
  <p style="margin-top:10px">Duis aute irure dolor in reprehenderit in voluptate velit esse cillum dolore eu fugiat nulla pariatur...</p>
  <span class="more">Read More</span>
</section>

<div class="abs svc" style="left:381px;top:478px;width:190px"><h3><span class="icon"><svg width="14" height="14"><path d="M2 5h10l-2 6H4z" fill="#fff"/></svg></span>Packaged Application</h3><p>Lorem ipsum dolor sit amet, consectetur adipisicing elit...</p><span class="more">Read More</span></div>
<div class="abs svc" style="left:593px;top:478px;width:190px"><h3><span class="icon"><svg width="14" height="14"><rect x="4" y="2" width="6" height="10" fill="#fff"/></svg></span>Enterprise Application</h3><p>Lorem ipsum dolor sit amet, consectetur adipisicing elit...</p><span class="more">Read More</span></div>
<div class="abs svc" style="left:381px;top:566px;width:190px"><h3><span class="icon"><svg width="14" height="14"><rect x="4" y="2" width="6" height="10" fill="#fff"/></svg></span>Digital Commerce</h3><p>Lorem ipsum dolor sit amet, consectetur adipisicing elit...</p><span class="more">Read More</span></div>
<div class="abs svc" style="left:593px;top:566px;width:190px"><h3><span class="icon"><svg width="14" height="14"><circle cx="7" cy="7" r="4" fill="none" stroke="#fff" stroke-width="2.5"/></svg></span>Application Development</h3><p>Lorem ipsum dolor sit amet, consectetur adipisicing elit...</p><span class="more">Read More</span></div>

<div class="abs register"></div>
<div class="abs field" style="left:96px;top:684px;width:172px">FIRST NAME...</div>
<div class="abs field" style="left:276px;top:684px;width:173px">LAST NAME...</div>
<div class="abs field" style="left:456px;top:684px;width:173px">EMAIL...</div>
<div class="abs btn" style="left:654px;top:681px;width:112px;height:28px;font-size:12px">REGISTER HERE</div>

<section class="abs" style="left:86px;top:756px;width:207px">
  <div class="rule-title">BLOG</div>
  <div class="item" style="margin-top:10px"><h4>Lorem Ipsum Dolor</h4><p>Lorem ipsum dolor sit amet, consectetur adipisicing elit...</p></div>
  <div class="item" style="margin-top:0;padding-top:0"><h4 style="margin-top:0">Lorem Ipsum Dolor</h4><p>Lorem ipsum dolor sit amet, consectetur adipisicing elit...</p></div>
  <div class="item"><h4>Lorem Ipsum Dolor</h4><p>Lorem ipsum dolor sit amet, consectetur adipisicing elit...</p></div>
</section>

<section class="abs" style="left:326px;top:756px;width:208px">
  <div class="rule-title">EVENTS</div>
  <div class="item" style="margin-top:10px;display:flex;gap:11px"><div class="date">12<br>Nov</div><div><h4>Lorem Ipsum Dolor</h4><p>Lorem ipsum dolor sit amet, consectetur adipisicing elit...</p></div></div>
  <div class="item" style="display:flex;gap:11px;padding-top:0"><div class="date">12<br>Nov</div><div><h4>Lorem Ipsum Dolor</h4><p>Lorem ipsum dolor sit amet, consectetur adipisicing elit...</p></div></div>
  <div class="item" style="display:flex;gap:11px"><div class="date">12<br>Nov</div><div><h4>Lorem Ipsum Dolor</h4><p>Lorem ipsum dolor sit amet, consectetur adipisicing elit...</p></div></div>
</section>

<section class="abs" style="left:567px;top:756px;width:208px">
  <div class="rule-title">REQUEST A CALLBACK</div>
  <p style="margin-top:10px;line-height:12.5px">Lorem ipsum dolor sit amet, consectetur adipi-sicing elit...</p>
  <div class="field" style="width:173px;margin-top:10px">NAME...</div>
  <div class="field" style="width:173px;margin-top:10px">PHONE...</div>
  <div class="field" style="width:173px;margin-top:10px">WHEN...</div>
  <div class="btn" style="width:70px;height:24px;margin-top:10px;font-size:12px">SUBMIT</div>
</section>

<footer class="abs footer">
  <div class="abs foot" style="left:87px;top:24px"><h5>SITE LINKS</h5><ul><li>Home</li><li>About Us</li><li>Clients</li><li>Our Services</li><li>Careers</li><li>Contact Us</li></ul></div>
  <div class="abs vsep" style="left:209px;top:52px"></div>
  <div class="abs foot" style="left:255px;top:24px"><h5>ABOUT US</h5><ul><li>Lorem Ipsum</li><li>Dolor Sit Amet</li><li>Consectetur</li><li>Adipsicing Elit.</li></ul></div>
  <div class="abs vsep" style="left:390px;top:52px"></div>
  <div class="abs foot" style="left:410px;top:24px;width:180px"><h5>TESTIMONIALS</h5>
    <div style="display:flex;gap:8px">
      <div role="img" aria-label="Portrait of the client" style="width:33px;height:33px;flex:none;background:linear-gradient(#9a8a80,#4a4f5a)"></div>
      <div><div style="font-size:8px;color:var(--green-dark)">Darren Pike</div><p style="font-size:9px;line-height:14.5px;color:#666;margin-top:3px">"Lorem ipsum dolor sit tetuer adipiscing elit, sed diam nummy nibh euismod.ut laoreet dolore magna aliquam rat volutpat. Ut wisi enim ad minim."</p></div>
    </div>
  </div>
  <div class="abs vsep" style="left:595px;top:52px"></div>
  <div class="abs foot" style="left:626px;top:24px;width:160px"><h5>CONTACT INFORMATIONS:</h5><ul><li>Address: Lorem ipsum dolor</li><li>Street,123</li><li>E-mail: info@bluefern-mail.com</li><li>Phone: +14 20 63 71 85</li></ul></div>
</footer>
<div class="abs bottom"><span>Copyright 2014 Bluefern. All Rights Reserved.</span><span>Privacy Policy | Terms &amp; Condition</span></div>
</body>
</html>
```